2018 TVPAC Conference Theme Artwork

We need artwork designed around the theme of this year's human resources conference. The theme is "Celebrating 20 Years Together Towards Tomorrow". The artwork should be designed as a 4x6 postcard and will eventually be adapted/reformatted to use on the registration website, sales materials, e-newsletters, conference guide cover and signage.

Target Market(s)

Attendees are human resources professionals. Exhibitors and sponsors are companies who want to sell their products/services to human resource professionals

Colors

Designer to choose colors to be used in the design.

Requirements
Must have
• NO BORING PIXVAULT IMAGERY PLEASE.
• Theme: Celebrating 20 Years Together Towards Tomorrow
• Event: 20th Annual TVPA Conference
• Dates/Times: Tuesday, May 15, 2018, 12:30pm - 5:00pm and Wednesday, May 16, 2018 7:30am - 5:30pm
• Website: tvpaconference.example
• Location: The HALL at the Corvane Manchester
Nice to have
• Engaging, celebratory, visually attractive
Should not have
• NO BORING PIXVAULT IMAGERY.

```html
<!DOCTYPE html>
<html lang="en">
<head>
<meta charset="utf-8">
<title>TVPA Conference Postcard</title>
<link href="https://fonts.googleapis.com/css2?family=Dancing+Script:wght@600&family=Lora:wght@700&family=Open+Sans:wght@400;600;700&display=swap" rel="stylesheet">
<style>
  :root{
    --board:#3b3b3b;
    --navy:#0f4a86;
    --sky:#b6dde9;
    --grey-arc:#9a9a9a;
    --paper:#ffffff;
    --stamp:#ececec;
    --rule:#d9d9d9;
    --ink:#222a33;
  }
  *{box-sizing:border-box;margin:0;padding:0}
  html,body{width:850px;height:1200px;overflow:hidden}
  body{background:var(--board);position:relative;font-family:"Open Sans",Arial,sans-serif}

  .card{position:absolute;background:var(--paper);box-shadow:0 10px 24px rgba(0,0,0,.55);overflow:hidden}
  .card--front{left:111px;top:122px;width:652px;height:433px}
  .card--back{left:111px;top:655px;width:649px;height:432px}

  /* front */
  .front-photo{position:absolute;inset:0 0 38px 0;
    background:
      radial-gradient(ellipse 130px 110px at 170px 340px,rgba(255,255,255,.85),rgba(255,255,255,0)),
      radial-gradient(ellipse 120px 110px at 330px 350px,rgba(255,255,255,.8),rgba(255,255,255,0)),
      radial-gradient(ellipse 140px 120px at 520px 330px,rgba(255,255,255,.8),rgba(255,255,255,0)),
      radial-gradient(ellipse 60px 70px at 200px 250px,rgba(226,196,170,.7),rgba(226,196,170,0)),
      radial-gradient(ellipse 60px 70px at 335px 245px,rgba(150,110,100,.55),rgba(150,110,100,0)),
      radial-gradient(ellipse 60px 70px at 480px 225px,rgba(230,200,160,.7),rgba(230,200,160,0)),
      linear-gradient(90deg,rgba(190,180,200,0) 55%,rgba(160,150,180,.45) 75%,rgba(190,180,200,.2) 100%),
      linear-gradient(180deg,#f6f2ee 0%,#ede7e5 26%,#d3cad2 50%,#c3bacb 70%,#dcd4da 100%)}
  .theme{position:absolute;left:30px;top:14px;color:var(--navy);display:flex;align-items:baseline;white-space:nowrap}
  .theme__script{font-family:"Dancing Script",cursive;font-size:42px;font-weight:600}
  .theme__number{font-family:"Lora",Georgia,serif;font-weight:700;font-size:54px;margin:0 0 0 12px;line-height:1}
  .theme__script--small{font-size:30px;margin-left:-2px}
  .tagline{position:absolute;left:31px;top:85px;color:var(--navy);font-weight:700;font-size:21.5px;letter-spacing:0}
  .event-name{position:absolute;left:31px;top:114px;color:var(--navy);font-weight:700;font-size:19.5px}
  .schedule{position:absolute;left:31px;top:148px;width:384px;height:56px;background:var(--navy);color:#fff;display:flex;align-items:center}
  .schedule__days{width:229px;padding-left:16px;font-size:16.5px;line-height:24px}
  .schedule__divider{width:1px;height:44px;background:#fff}
  .schedule__times{padding-left:19px;font-size:15px;line-height:24px}
  .org-name{position:absolute;right:18px;top:22px;width:130px;text-align:right;color:var(--navy);font-weight:700;font-size:15px;line-height:18px}
  .info-band{position:absolute;left:0;right:0;bottom:0;height:38px;background:var(--navy);color:#fff;display:flex;align-items:center;font-weight:700;font-size:16px;padding:0 22px 0 12px;white-space:nowrap}
  .info-band__item{display:flex;align-items:center;gap:9px}
  .info-band__divider{width:1px;height:24px;background:#fff;margin:0 18px 0 14px}
  .info-band__item--web{font-size:17px}

  /* back */
  .back-art{position:absolute;left:0;top:0}
  .back-org{position:absolute;left:40px;top:24px;width:180px;text-align:center;color:var(--navy);font-weight:700;font-size:15px;line-height:19px}
  .about-pill{position:absolute;left:52px;top:103px;width:152px;height:28px;border-radius:9px;background:var(--navy);border:2px solid #fff;box-shadow:0 3px 4px rgba(0,0,0,.25);color:#fff;font-size:15px;text-align:center;line-height:24px}
  .about-copy{position:absolute;left:17px;top:142px;width:272px;color:var(--ink);font-size:13.3px;line-height:18.6px}
  .about-copy p+p{margin-top:11px}
  .stamp-box{position:absolute;left:559px;top:16px;width:66px;height:64px;background:var(--stamp)}
  .address-line{position:absolute;left:439px;width:186px;height:1px;background:var(--rule)}
</style>
</head>
<body>

<section class="card card--front">
  <div class="front-photo" role="img" aria-label="Photo of three cheering businesswomen in white shirts in front of an office building"></div>

  <h1 class="theme">
    <span class="theme__script">Celebrating</span>
    <span class="theme__number">20</span>
    <span class="theme__script theme__script--small">Years</span>
  </h1>
  <h2 class="tagline">TOGETHER TOWARDS TOMORROW</h2>
  <p class="event-name">20th Annual TVPA Conference</p>

  <div class="schedule">
    <div class="schedule__days">Tuesday, May 15, 2018<br>Wednesday, May 16, 2018</div>
    <div class="schedule__divider"></div>
    <div class="schedule__times">12:30pm - 5:00pm<br>7:30am - 5:30pm</div>
  </div>

  <p class="org-name">Talent Valley People Alliance</p>

  <div class="info-band">
    <span class="info-band__item">
      <svg width="20" height="20" viewBox="0 0 20 20" aria-hidden="true"><circle cx="10" cy="10" r="8.5" fill="none" stroke="#fff" stroke-width="1.6"/><path d="M10 4.5a3.3 3.3 0 0 0-3.3 3.3c0 2.4 3.3 6.5 3.3 6.5s3.3-4.1 3.3-6.5A3.3 3.3 0 0 0 10 4.5z" fill="#fff"/><circle cx="10" cy="7.8" r="1.2" fill="#0f4a86"/></svg>
      The HALL at the Corvane Manchester
    </span>
    <span class="info-band__divider"></span>
    <span class="info-band__item info-band__item--web">
      <svg width="16" height="16" viewBox="0 0 20 20" aria-hidden="true" fill="none" stroke="#fff" stroke-width="1.6"><circle cx="10" cy="10" r="8"/><ellipse cx="10" cy="10" rx="3.5" ry="8"/><path d="M2 10h16M3.5 5.5h13M3.5 14.5h13"/></svg>
      tvpaconference.example
    </span>
  </div>
</section>

<section class="card card--back">
  <svg class="back-art" width="649" height="432" viewBox="0 0 649 432">
    <defs>
      <clipPath id="panel-clip"><path d="M0 0H214C302 90 348 300 296 432H0Z"/></clipPath>
      <linearGradient id="photo-tone" x1="0" y1="0" x2="0" y2="1">
        <stop offset="0" stop-color="#b6dde9"/>
        <stop offset=".28" stop-color="#f4f7f9"/>
        <stop offset=".6" stop-color="#8a8f9e"/>
        <stop offset="1" stop-color="#2a3550"/>
      </linearGradient>
    </defs>
    <path d="M0 0H245C335 90 378 300 318 432H0Z" fill="var(--grey-arc)"/>
    <path d="M0 0H228C318 90 362 300 306 432H0Z" fill="var(--navy)"/>
    <path d="M0 0H214C302 90 348 300 296 432H0Z" fill="var(--sky)"/>
    <g clip-path="url(#panel-clip)" role="img" aria-label="Photo of a business team joining hands in a high five">
      <rect x="0" y="290" width="360" height="142" fill="url(#photo-tone)"/>
    </g>
  </svg>

  <p class="back-org">Talent Valley People Alliance</p>
  <div class="about-pill">ABOUT THE EVENT</div>
  <div class="about-copy">
    <p>Thank you for a fantastic 2017 Conference! Stay tuned for our 2018 dates, coming soon.</p>
    <p>We bring Human Resource Professionals together from all types of companies and organizations, vendors, and educational experts to promote HR knowledge, networking, and the HR profession</p>
  </div>

  <div class="stamp-box"></div>
  <div class="address-line" style="top:150px"></div>
  <div class="address-line" style="top:178px"></div>
  <div class="address-line" style="top:206px"></div>
  <div class="address-line" style="top:234px"></div>
</section>

</body>
</html>
```